IT Company requires new Business Card design.

Over the years we have had a few different business card designs. We are now due for new cards across the board for all staff. We felt this would be a good time to start fresh with a new design. Our traditional card simply had our details on the front, and a list of services on the back. We don't particularly need the list of services, we have had cards where the only thing on the rear of the card was our logo.
Feel free to be creative, we would like our tag line "Complete IT Management" to appear at some point, doesn't necessarily have to be with the logo.
I have attached samples and drafts of various previous cards we have used over the years.

```html
<!DOCTYPE html>
<html lang="en">
<head>
<meta charset="utf-8">
<title>Harbour Systems – Business Card</title>
<link rel="stylesheet" href="https://fonts.googleapis.com/css2?family=Open+Sans:wght@400;600;700&family=Roboto:wght@700&display=swap">
<style>
  :root {
    --canvas: #ececec;
    --card: #ffffff;
    --brand-slate: #5f6d78;
    --band-dark: #48494b;
    --band-slate: #65737d;
    --text-light: #ffffff;
    --text-soft: #e4e9ec;
    --divider: #8a8b8d;
    --url-ink: #3d3f42;
  }
  * { box-sizing: border-box; margin: 0; padding: 0; }
  html, body {
    width: 1034px; height: 1200px; overflow: hidden;
    background: var(--canvas);
    font-family: "Open Sans", Arial, sans-serif;
  }
  .canvas { position: relative; width: 1034px; height: 1200px; }

  .card {
    position: absolute; left: 75px; width: 901px; height: 514px;
    background: var(--card); border-radius: 30px; overflow: hidden;
    box-shadow: 0 2px 6px rgba(0,0,0,0.12);
  }
  .card--front { top: 69px; }
  .card--back { top: 631px; }

  /* Front: brand lockup */
  .brand {
    position: absolute; left: 218px; top: 56px;
    display: flex; align-items: center; gap: 28px;
  }
  .brand__square { width: 150px; height: 150px; background: var(--brand-slate); }
  .brand__name {
    font-family: "Roboto", Arial, sans-serif; font-weight: 700;
    color: var(--brand-slate); line-height: 0.95; text-transform: uppercase;
  }
  .brand__name span { display: block; }
  .brand__line1 { font-size: 80px; letter-spacing: 1px; }
  .brand__line2 { font-size: 41px; letter-spacing: 1px; }

  /* Front: contact band */
  .contact-band {
    position: absolute; left: 0; top: 286px; width: 100%; height: 168px;
    background: var(--band-dark); color: var(--text-light);
  }
  .person {
    position: absolute; right: 520px; top: 18px; text-align: right;
  }
  .person__name { font-size: 26px; font-weight: 700; line-height: 1.3; }
  .person__role { font-size: 21px; line-height: 1.4; color: var(--text-soft); }
  .person__mobile {
    margin-top: 14px; font-size: 21px; display: flex;
    justify-content: flex-end; align-items: center; gap: 10px;
  }
  .band-divider {
    position: absolute; left: 400px; top: 22px; width: 1px; height: 124px;
    background: var(--divider);
  }
  .contact-list {
    position: absolute; left: 420px; top: 8px; list-style: none;
  }
  .contact-list li {
    display: flex; align-items: center; gap: 12px;
    font-size: 21px; height: 38px;
  }
  .icon { width: 20px; height: 20px; fill: var(--text-light); flex: none; }

  .tagline-band {
    position: absolute; left: 0; top: 454px; width: 100%; height: 60px;
    background: var(--band-slate); color: var(--text-soft);
    display: flex; align-items: center; justify-content: center;
    font-size: 23px; letter-spacing: 5px; text-transform: uppercase;
  }

  /* Back */
  .back-name {
    position: absolute; left: 0; top: 88px; width: 100%; text-align: center;
    font-family: "Roboto", Arial, sans-serif; font-weight: 700;
    color: var(--brand-slate); text-transform: uppercase; line-height: 1;
  }
  .back-name span { display: block; }
  .back-name__line1 { font-size: 118px; }
  .back-name__line2 { font-size: 118px; margin-top: 12px; }
  .back-url {
    position: absolute; left: 0; top: 464px; width: 100%; text-align: center;
    font-size: 24px; letter-spacing: 2px; color: var(--url-ink);
  }
</style>
</head>
<body>
<main class="canvas">

  <section class="card card--front" aria-label="Card front">
    <div class="brand">
      <div class="brand__square"></div>
      <div class="brand__name">
        <span class="brand__line1">Harbour</span>
        <span class="brand__line2">Systems</span>
      </div>
    </div>

    <div class="contact-band">
      <div class="person">
        <p class="person__name">Mark Ellison</p>
        <p class="person__role">Operation Manager</p>
        <p class="person__mobile">
          <svg class="icon" viewBox="0 0 20 20" aria-hidden="true"><path d="M6 1h8a1.5 1.5 0 0 1 1.5 1.5v15A1.5 1.5 0 0 1 14 19H6a1.5 1.5 0 0 1-1.5-1.5v-15A1.5 1.5 0 0 1 6 1zm0.5 2.5v8h7v-8zm1 10v1.5h1.5v-1.5zm2.5 0v1.5h1.5v-1.5zm-2.5 2.5v1.3h1.5v-1.3zm2.5 0v1.3h1.5v-1.3z"/></svg>
          0412 583 906
        </p>
      </div>
      <div class="band-divider"></div>
      <ul class="contact-list">
        <li>
          <svg class="icon" viewBox="0 0 20 20" aria-hidden="true"><path d="M10 1a9 9 0 1 0 0 18 9 9 0 0 0 0-18zm0 1.6a7.4 7.4 0 1 1 0 14.8 7.4 7.4 0 0 1 0-14.8zM7.2 5.2l1.6-.4 1 2.6-1.1.9a6 6 0 0 0 2.2 2.6l1-1 2.4 1.3-.5 1.6c-3.5.3-6.9-3.8-6.6-7.6z"/></svg>
          08 9326 5140
        </li>
        <li>
          <svg class="icon" viewBox="0 0 20 20" aria-hidden="true"><path d="M5 2h10v5H5zM2 8h16v7h-3v3H5v-3H2zm4 5v3.5h8V13z"/></svg>
          08 9326 5140
        </li>
        <li>
          <svg class="icon" viewBox="0 0 20 20" aria-hidden="true"><path d="M2 6l8-4 8 4v11H2zm2 1.2L10 11l6-3.8L10 4z"/></svg>
          mark@harboursystems.com.au
        </li>
        <li>
          <svg class="icon" viewBox="0 0 20 20" aria-hidden="true"><path d="M10 1a9 9 0 1 0 0 18 9 9 0 0 0 0-18zm-1 2.2v3.3H6.3A7 7 0 0 1 9 3.2zm2 0a7 7 0 0 1 2.7 3.3H11zM4.3 8.5H9v3H4.3a7 7 0 0 1 0-3zm6.7 0h4.7a7 7 0 0 1 0 3H11zm-4.7 5H9v3.3a7 7 0 0 1-2.7-3.3zm4.7 0h2.7a7 7 0 0 1-2.7 3.3z"/></svg>
          www.harboursystems.com.au
        </li>
      </ul>
    </div>

    <div class="tagline-band">Complete IT Management</div>
  </section>

  <section class="card card--back" aria-label="Card back">
    <div class="back-name">
      <span class="back-name__line1">Harbour</span>
      <span class="back-name__line2">Systems</span>
    </div>
    <p class="back-url">www.harboursystems.com.au</p>
  </section>

</main>
</body>
</html>
```